Yoga/movement guide/teacher for adult yoga practice and kid yoga

What is the positioning or mission statement of your company? to guide individuals in a yoga-based safe and sustainable movement practice applicable to all ages and body types. Currently my focus is working with children in daycare and school settings, but my goal is to expand into private yoga practice for adults, and potentially as part of rented space in studios. I hope to find a way to work with children AND adults (so would love for logo to be appealing to both), but current focus is with children based on need and demand in the community. yoga for children also compliments my backround as a pediatrician/neonatologist, and I greatly miss interacting with children. I also want to emphasize a yoga/movement practice that is focused more on what one feels internally through movement. NOT what one looks like asthetically. I believe in removing all mirrors from yoga/movement practice. It should be an experience of movement/poses/yoga through appropriate cueing and education. It is not about the details of how far the knee should bend, or how high the leg should be. Focusing on foudation first, core, then core engagement and ultimately expression of poses/movements. A focus on strength, stability and mobility, not just flexibility, which is the common perception/association with yoga. I also want individuals to learn to be an advocate of their own health. Through guidance, I hope for individuals to connect with their body so they know themselves so well to be able to advocate for themselves in the modern healthcare world. This internal experience and connection is so essential in a world where modern medicine has become a business and it is all about making a dollar. the connection with patients is lost, and individuals need to learn to empower themselves and through their new found voice to be able to articulate what is wrong.<br/>Does your company have a tagline or slogan that should be included with the logo? "Find Your Inner Momentum"<br/>What do you hope your company can be known for? Accessible yoga for a sustained practice. A guided movement practice where one gains information and knowledge of oneself through a mind/body connection. For one feel good physically with a new awaraness of their internal radiance that exists in all beings. Physical rejuvenation egnites a light and increases energy to flow through the physical body, which ultimately tranlates into works of kindness for others and out in the world. <br/>What color palettes might you prefer? why? love the colors currently chosen<br/>Where will the logo be primarily used? initially business cards, but hopefully future websites, t-shirts, and potentially local magazine adds. Also starting with a small couple of banners for community events in the area. I currently practice as a nomad out of my car :)<br/>Are there any elements you would prefer to see in the logo? Movement. A modern depiction of a human body/figure practicing movement. Hoping to avoid a stereotypical yoga pose per say, just because I want to people to think of it more of a movement practice with yoga roots. Modern yoga. There are elements of breathing and connecting with oneself through the flow of breath and movement, but I do not focus on the meditative/cerebral aspect of the yoga practice. What I teach is almost reaching a meditative state through movement. I personally don't practice, nor resonate with just seated meditation. just not my thing :)<br/>In your opinion, what defines a well-designed logo? curiosity. enough info for individuals to think they know what it means, but want to know more. invokes curiosity, but not too abstract. Reproducible. not too complicated. I want also to invoke a community feel, so a design that appeals to all people within a community. <br/>What is your preference in reference to icons, typography, spokespeople (characters), etc.? modern design. I love the idea of a logo for my purposes, to invoke a sense of movement from within. So not too static. <br/>What words or icons must be included in the logo? movement with yoga roots. <br/>What logos do you like and why? A representation, but not exact. I think some ambiguity is intriguing for others, and also memorable. I want it to be an artistic representation of movement/yoga<br/>What logos do you dislike and why? too busy, too loud. <br/>In your opinion, what is the primary purpose for a logo? association<br/>Who is the primary target audience? (who is most likely to use your services/product?) Children and their parents, but ultimately to expand into teaching adults. I even have aspirations of prenatal and post-natal yoga. Potentially incorporating infants. <br/>Who currently uses your product the most? n/a (working in schools/daycare currently. It is currently all volunteer)<br/>Are you pleased with the range of people your company serves? n/a<br/>Are you looking to expand, modify, or completely change your target audience? or will it remain the same? yes! expand into an adult audience. <br/>How do you plan to focus on your target audience? currently by working through schools and daycares. hopefully ultimately through after school care programs and then offering kid yoga in an existing yoga studio (working on this with Q Studio in Ridgeland, currently)<br/>What are your main forms of advertising? word of mouth, schools, daycares. Happy kids talking to their parents about the yoga class they took and happy teachers :)<br/>How do most customers find out about your company?<br/>Which gender are you targeting? All genders! However, with kid yoga, often the maternal individual in the child's life is more involved with decision making as far as extracurricular activities

Target Market(s)

individuals and families interested in wellness and feeling great

Contact Information for Business Card

Dana Whitford
Yoga Instructor
RYT-200, RCYT

certified yoga teacher for adults and children

Colors

Designer to choose colors to be used in the design.

Requirements
Must have
• "Find Your Inner Momentum"
Nice to have
• logo with same colors

```html
<!DOCTYPE html>
<html lang="en">
<head>
<meta charset="utf-8">
<title>Lumen Motion – Business Card</title>
<link href="https://fonts.googleapis.com/css2?family=Arimo:wght@400;700&display=swap" rel="stylesheet">
<style>
  :root {
    --bg: #3a3a3c;
    --card-dark: #17161b;
    --card-light: #ffffff;
    --sun: #f7d93a;
    --teal: #5ec8d3;
    --ink: #1c1c1c;
    --grey: #8a8a8a;
  }
  * { margin: 0; padding: 0; box-sizing: border-box; }
  html, body { width: 1200px; height: 1200px; overflow: hidden; }
  body {
    background: var(--bg);
    font-family: "Arimo", Arial, sans-serif;
    position: relative;
  }
  .card {
    position: absolute;
    left: 240px;
    width: 720px;
    height: 400px;
    box-shadow: 0 12px 30px rgba(0,0,0,.35);
  }
  .card-back {
    top: 130px;
    background: var(--card-dark);
    border-radius: 70px 0 70px 0;
    display: flex;
    align-items: center;
    justify-content: center;
  }
  .card-front {
    top: 660px;
    background: var(--card-light);
    border-radius: 0 70px 0 70px;
  }
  .brand {
    display: flex;
    flex-direction: column;
    align-items: flex-start;
  }
  .brand-mark {
    display: flex;
    align-items: center;
    gap: 16px;
  }
  .brand-dot {
    width: 64px; height: 64px;
    border-radius: 50%;
    background: var(--sun);
  }
  .brand-name {
    font-size: 44px;
    font-weight: 400;
    color: var(--grey);
    letter-spacing: 1px;
  }
  .brand-tagline {
    margin-top: 8px;
    margin-left: 80px;
    font-size: 13px;
    letter-spacing: 3px;
    text-transform: uppercase;
    color: var(--teal);
  }
  .card-front .brand {
    position: absolute;
    right: 50px;
    top: 120px;
  }
  .card-front .brand-name { font-size: 38px; }
  .card-front .brand-dot { width: 56px; height: 56px; }
  .card-front .brand-tagline { margin-left: 72px; font-size: 12px; }
  .person {
    position: absolute;
    left: 60px;
    top: 50px;
  }
  .person-name {
    font-size: 22px;
    font-weight: 700;
    color: var(--sun);
    text-transform: uppercase;
  }
  .person-role {
    font-size: 17px;
    color: var(--ink);
    margin-top: 2px;
  }
  .contact {
    position: absolute;
    left: 60px;
    top: 175px;
    list-style: none;
    font-size: 17px;
    color: var(--ink);
  }
  .contact li {
    display: flex;
    align-items: center;
    gap: 8px;
    line-height: 26px;
  }
  .contact svg { width: 16px; height: 16px; fill: var(--sun); flex: none; }
  .address {
    position: absolute;
    left: 60px;
    top: 275px;
    font-size: 17px;
    line-height: 24px;
    color: var(--ink);
    font-style: normal;
  }
  .social {
    position: absolute;
    right: 60px;
    bottom: 40px;
    display: flex;
    gap: 6px;
  }
  .social span {
    width: 30px; height: 30px;
    border: 2px solid var(--ink);
    border-radius: 50%;
  }
</style>
</head>
<body>

<section class="card card-back">
  <div class="brand">
    <div class="brand-mark">
      <span class="brand-dot"></span>
      <span class="brand-name">Lumen Motion</span>
    </div>
    <span class="brand-tagline">Find Your Inner Momentum</span>
  </div>
</section>

<section class="card card-front">
  <div class="person">
    <p class="person-name">Dana Whitford</p>
    <p class="person-role">Managing Director</p>
  </div>

  <ul class="contact">
    <li>
      <svg viewBox="0 0 16 16" aria-hidden="true"><path d="M3 1h3l1 4-2 1c1 2 3 4 5 5l1-2 4 1v3c0 1-1 2-2 2C7 15 1 9 1 3c0-1 1-2 2-2z"/></svg>
      044-555 018 274
    </li>
    <li>
      <svg viewBox="0 0 16 16" aria-hidden="true"><path d="M1 3h14v10H1z M2 4l6 5 6-5" stroke="#fff" stroke-width="1"/></svg>
      hello@lumenmotion.com
    </li>
    <li>
      <svg viewBox="0 0 16 16" aria-hidden="true"><circle cx="8" cy="8" r="7"/><path d="M1 8h14M8 1c-3 4-3 10 0 14M8 1c3 4 3 10 0 14" stroke="#fff" stroke-width="1" fill="none"/></svg>
      www.lumenmotion.com
    </li>
  </ul>

  <address class="address">
    12345, Address Goes Here<br>
    Country Name, 123456
  </address>

  <div class="brand">
    <div class="brand-mark">
      <span class="brand-dot"></span>
      <span class="brand-name">Lumen Motion</span>
    </div>
    <span class="brand-tagline">Find Your Inner Momentum</span>
  </div>

  <div class="social" aria-label="Social media links">
    <span></span><span></span><span></span><span></span>
  </div>
</section>

</body>
</html>
```